Oakmere Animal Care Group of Central Pennsylvania

I need a business card design for a new company in Harrisburg PA called "Animal Care Oakmere Group of Central PA". I will be providing relief services for veterinarians who need coverage during vacations; sick/maternity leave, etc. I would like to see the veterinarian symbol incorporated in the design in combination with animals (dogs /cats/birds/reptiles an pocket pets). Include My full name: Tomás R. Quintaval DVM, MLAS, BS. Also include my e mail (dvmtrq@mailbrook.net) and phone number 5552846017

Target Market(s)

Small Animal Veterinarian, practice owner

Industry/Entity Type

Business

Contact Information for Business Card

Oakmere Animal Care Group of Central PA

Font styles to use
Script

Requirements
Must have
• Veterinarian caduceus (see image) and Small animals (pets) within the logo.
Nice to have
• Give a sense of relaxation (vacationing)
Should not have
• Large animals, i.e. horses, cows, zoo animals...

```html
<!DOCTYPE html>
<html lang="en">
<head>
<meta charset="utf-8">
<title>Animal Care Oakmere Group of Central PA — Business Card</title>
<link rel="stylesheet" href="https://fonts.googleapis.com/css2?family=Cinzel:wght@600&family=Great+Vibes&family=Open+Sans:wght@400&display=swap">
<style>
  :root {
    --stage: #e9e7e4;
    --paper: #ffffff;
    --ink: #1c1c1c;
    --brand-red: #c8353c;
    --soft-grey: #c9c9c9;
    --band-black: #111111;
  }
  * { margin: 0; padding: 0; box-sizing: border-box; }
  html, body { width: 1200px; height: 818px; overflow: hidden; background: var(--stage); }
  .card {
    position: absolute; left: 140px; top: 146px;
    width: 920px; height: 526px;
    background: var(--paper);
    box-shadow: 0 12px 30px rgba(0,0,0,.18);
    overflow: hidden;
  }
  .card-swoosh { position: absolute; inset: 0; width: 100%; height: 100%; }
  .brand {
    position: absolute; left: 50px; top: 120px; width: 360px;
    display: flex; flex-direction: column; align-items: center; gap: 20px;
  }
  .brand-mark {
    width: 124px; height: 124px; border-radius: 50%;
    border: 9px solid var(--brand-red);
  }
  .brand-name {
    font-family: "Cinzel", serif; font-weight: 600;
    font-size: 19px; line-height: 1.35; letter-spacing: .4px;
    color: var(--ink); text-align: center; white-space: nowrap;
  }
  .holder-name {
    position: absolute; left: 420px; top: 42px;
    font-family: "Great Vibes", cursive; font-size: 50px; line-height: 1.2;
    color: var(--brand-red); white-space: nowrap;
  }
  .contact {
    position: absolute; left: 440px; top: 150px;
    display: flex; flex-direction: column; gap: 16px;
    font-family: "Open Sans", sans-serif; font-size: 23px; color: var(--ink);
  }
  .contact-row { display: flex; align-items: center; gap: 14px; white-space: nowrap; }
  .contact-icon { width: 24px; height: 24px; flex: none; }
</style>
</head>
<body>
  <div class="card">
    <svg class="card-swoosh" viewBox="0 0 920 526" preserveAspectRatio="none" aria-hidden="true">
      <path d="M0,400 C420,490 820,400 900,0 L920,0 L920,526 L0,526 Z" fill="var(--soft-grey)"/>
      <path d="M0,430 C430,515 845,425 920,20 L920,526 L0,526 Z" fill="var(--brand-red)"/>
      <path d="M0,460 C440,540 860,455 920,80 L920,526 L0,526 Z" fill="var(--band-black)"/>
    </svg>

    <div class="brand">
      <div class="brand-mark"></div>
      <div class="brand-name">Animal Care Oakmere Group<br>of Central PA</div>
    </div>

    <div class="holder-name">Tomás R. Quintaval</div>

    <div class="contact">
      <div class="contact-row">
        <svg class="contact-icon" viewBox="0 0 26 26" aria-label="Phone">
          <rect width="26" height="26" fill="var(--brand-red)"/>
          <path d="M8 6c1 0 2 3 2 4s-1 1-1 2 3 4 4 4 1-1 2-1 4 1 4 2-2 3-3 3C11 20 6 15 6 9c0-1 1-3 2-3z" fill="#fff"/>
        </svg>
        <span>5552846017</span>
      </div>
      <div class="contact-row">
        <svg class="contact-icon" viewBox="0 0 26 26" aria-label="Email">
          <rect width="26" height="26" fill="var(--brand-red)"/>
          <rect x="5" y="8" width="16" height="11" fill="none" stroke="#fff" stroke-width="1.6"/>
          <path d="M5 8l8 6 8-6" fill="none" stroke="#fff" stroke-width="1.6"/>
        </svg>
        <span>dvmtrq@mailbrook.net</span>
      </div>
    </div>
  </div>
</body>
</html>
```